Corporate Business Card

Very professional, Modern, Not to busy, include phone address email, website
(541) 617-4930, 18761 52nd Avenue S, Dalton, OR 97418, martin@plumlinegroup.com, varkoworks.com

Target Market(s)

Manufacturing

Industry/Entity Type

Aero, machining, manufacturing, Off road racing

Contact Information for Business Card

Phone, address email, website

```html
<!DOCTYPE html>
<html lang="en">
<head>
<meta charset="UTF-8">
<title>Varko Works Business Card</title>
<link href="https://fonts.googleapis.com/css2?family=Raleway:wght@400;500;700;800&display=swap" rel="stylesheet">
<style>
  :root {
    --navy: #173670;
    --red: #d2232a;
    --ink: #3a3a3a;
    --muted: #555b66;
    --paper: #ffffff;
    --backdrop: #3b3b3b;
  }
  * { box-sizing: border-box; margin: 0; padding: 0; }
  html, body { width: 1200px; height: 1200px; overflow: hidden; }
  body {
    background: var(--backdrop);
    font-family: "Raleway", sans-serif;
    display: flex;
    flex-direction: column;
    align-items: center;
    justify-content: center;
    gap: 44px;
  }
  .card {
    position: relative;
    width: 820px;
    height: 470px;
    border-radius: 28px;
    overflow: hidden;
  }
  .card--front { background: var(--paper); }
  .card--back { background: var(--navy); }

  .brand {
    position: absolute;
    display: flex;
    align-items: center;
    gap: 12px;
    font-weight: 800;
    letter-spacing: 0.02em;
    text-transform: uppercase;
    white-space: nowrap;
  }
  .brand__mark { display: block; background: var(--red); flex: none; }
  .card--front .brand { top: 58px; right: 70px; color: var(--navy); font-size: 42px; }
  .card--front .brand__mark { width: 18px; height: 18px; }
  .brand-rule { position: absolute; height: 2px; }
  .card--front .brand-rule { top: 124px; right: 150px; width: 300px; background: var(--navy); }

  .identity { position: absolute; left: 62px; top: 268px; }
  .identity__name { color: var(--red); font-weight: 700; font-size: 34px; letter-spacing: 0.01em; line-height: 1; }
  .identity__title { color: var(--muted); font-weight: 500; font-size: 17px; letter-spacing: 0.04em; margin-top: 6px; }

  .divider { position: absolute; left: 62px; right: 62px; top: 338px; height: 1px; background: var(--navy); }

  .contacts { position: absolute; top: 356px; left: 62px; right: 40px; display: flex; gap: 40px; }
  .contacts__col { display: flex; flex-direction: column; gap: 10px; }
  .contact { display: flex; align-items: center; gap: 10px; color: var(--ink); font-size: 17px; font-weight: 500; white-space: nowrap; }
  .contact svg { width: 20px; height: 20px; flex: none; fill: var(--red); }

  .footer-bands { position: absolute; left: 0; bottom: 0; width: 820px; height: 60px; }

  .card--back .brand { left: 50%; top: 50%; transform: translate(-50%, -60%); color: #fff; font-size: 76px; gap: 20px; }
  .card--back .brand__mark { width: 30px; height: 30px; }
  .card--back .brand-rule { left: 170px; width: 300px; top: 300px; background: #fff; }
</style>
</head>
<body>
  <section class="card card--front" aria-label="Card front">
    <div class="brand"><span class="brand__mark"></span>Varko Works</div>
    <div class="brand-rule"></div>

    <div class="identity">
      <p class="identity__name">JOHN DOE</p>
      <p class="identity__title">CEO | FOUNDER</p>
    </div>
    <div class="divider"></div>

    <div class="contacts">
      <div class="contacts__col">
        <p class="contact">
          <svg viewBox="0 0 24 24" aria-hidden="true"><path d="M6.6 10.8a15.1 15.1 0 0 0 6.6 6.6l2.2-2.2a1 1 0 0 1 1-.25 11.4 11.4 0 0 0 3.6.57 1 1 0 0 1 1 1V20a1 1 0 0 1-1 1A17 17 0 0 1 3 4a1 1 0 0 1 1-1h3.5a1 1 0 0 1 1 1c0 1.25.2 2.45.57 3.57a1 1 0 0 1-.25 1z"/></svg>
          (541) 617-4930
        </p>
        <p class="contact">
          <svg viewBox="0 0 24 24" aria-hidden="true"><path d="M12 2a10 10 0 1 0 0 20 10 10 0 0 0 0-20zm6.9 6h-2.9a15.6 15.6 0 0 0-1.4-3.6A8 8 0 0 1 18.9 8zM12 4c.8 1.2 1.5 2.5 1.9 4h-3.8c.4-1.4 1.1-2.8 1.9-4zM4.3 14a8 8 0 0 1 0-4h3.4a16 16 0 0 0 0 4zm.8 2h3a15.6 15.6 0 0 0 1.4 3.6A8 8 0 0 1 5.1 16zm3-8h-3a8 8 0 0 1 4.3-3.6C8.8 5.5 8.4 6.7 8.1 8zM12 20c-.8-1.2-1.5-2.5-1.9-4h3.8c-.4 1.4-1.1 2.8-1.9 4zm2.3-6H9.7a14.7 14.7 0 0 1 0-4h4.6a14.7 14.7 0 0 1 0 4zm.3 5.6c.6-1.1 1.1-2.3 1.4-3.6h2.9a8 8 0 0 1-4.3 3.6zm1.7-5.6a16 16 0 0 0 0-4h3.4a8 8 0 0 1 0 4z"/></svg>
          varkoworks.com
        </p>
      </div>
      <div class="contacts__col">
        <p class="contact">
          <svg viewBox="0 0 24 24" aria-hidden="true"><path d="M2 5h20v14H2zm2 2v.4l8 5.2 8-5.2V7zm16 2.8-8 5.2-8-5.2V17h16z"/></svg>
          martin@plumlinegroup.com
        </p>
        <p class="contact">
          <svg viewBox="0 0 24 24" aria-hidden="true"><path d="M12 2a7 7 0 0 0-7 7c0 5.2 7 13 7 13s7-7.8 7-13a7 7 0 0 0-7-7zm0 9.5a2.5 2.5 0 1 1 0-5 2.5 2.5 0 0 1 0 5z"/></svg>
          18761 52nd Avenue S Dalton, OR 97418
        </p>
      </div>
    </div>

    <svg class="footer-bands" viewBox="0 0 820 60" aria-hidden="true">
      <polygon points="0,38 530,24 530,60 0,60" fill="var(--red)"/>
      <polygon points="545,18 820,8 820,60 545,60" fill="var(--navy)"/>
    </svg>
  </section>

  <section class="card card--back" aria-label="Card back">
    <div class="brand"><span class="brand__mark"></span>Varko Works</div>
    <div class="brand-rule"></div>
  </section>
</body>
</html>
```